Printer Cartridges Supplier Namecard

Attached is my company logo and the design of my current namecard. I would like to have a more special look for it. Can have a little cuteness too rather than those normal standard feel. I'm a supplier mainly dealing with original and compatible printer toner cartridges, some other products like paper supplies as well.

Target Market(s)

Companies, businesses, corporates

Industry/Entity Type

It Company

Contact Information for Business Card

Logo, name, contact, address, supplies and maybe a slogan

Colors
85cae6
33a6d7
3176b5
0255a3
0792cd
85abd2

Requirements
Must have
• Logo, name, contact and address basic details.
• Must include some pictures, not just rearrange what I'm currently having.
Nice to have
• Be creative and bold, a diiferent traditional feel.

```html
<!DOCTYPE html>
<html lang="en">
<head>
<meta charset="utf-8">
<title>Tonerbay Namecard</title>
<link rel="stylesheet" href="https://fonts.googleapis.com/css2?family=Open+Sans:wght@400;600&display=swap">
<style>
  :root {
    --sky: #62b4e3;
    --sky-deep: #4fa6d9;
    --ink: #2b2b2b;
    --rule: #d6d6d6;
    --paper: #ffffff;
    --backdrop: #eceef0;
    --thumb-copier: linear-gradient(160deg, #eef1f4, #9aa3ad);
    --thumb-paper: linear-gradient(160deg, #ffffff, #bcd3ea);
    --thumb-ink: linear-gradient(90deg, #3fb8e6, #e0407f, #f2d13a, #222);
  }
  * { box-sizing: border-box; margin: 0; padding: 0; }
  html, body {
    width: 1200px; height: 900px; overflow: hidden;
    background: var(--backdrop);
    font-family: "Open Sans", sans-serif;
  }
  .canvas { position: relative; width: 1200px; height: 900px; }

  .card { position: absolute; box-shadow: 0 6px 18px rgba(0,0,0,.18); }

  /* Front */
  .card--front {
    left: 238px; top: 60px; width: 555px; height: 345px;
    background: var(--paper);
  }
  .holder { position: absolute; left: 36px; top: 66px; color: var(--ink); }
  .holder__name { font-size: 22px; font-weight: 600; color: var(--sky); line-height: 1.1; }
  .holder__role { font-size: 15px; margin-bottom: 22px; }
  .holder__address { font-size: 15px; line-height: 20px; margin-bottom: 14px; }
  .contact { list-style: none; font-size: 15px; line-height: 20px; }
  .contact li { display: flex; align-items: center; gap: 7px; }
  .contact svg { width: 10px; height: 10px; fill: var(--sky); flex: none; }
  .divider {
    position: absolute; left: 273px; top: 63px;
    width: 1px; height: 208px; background: var(--rule);
  }
  .front-brand {
    position: absolute; left: 274px; right: 0; top: 0; bottom: 0;
    display: flex; flex-direction: column; align-items: center; justify-content: center; gap: 14px;
  }
  .front-brand__mark { width: 120px; height: 120px; border-radius: 18px; background: var(--sky); }
  .front-brand__name { font-size: 26px; font-weight: 600; color: var(--sky); }

  /* Back */
  .card--back {
    left: 457px; top: 518px; width: 560px; height: 344px;
    background: var(--sky); color: var(--paper); text-align: center;
  }
  .brand {
    display: flex; align-items: center; justify-content: center; gap: 12px;
    margin-top: 62px;
  }
  .brand__square { width: 40px; height: 40px; border-radius: 6px; background: var(--paper); }
  .brand__name { font-size: 50px; font-weight: 600; line-height: 1; }
  .brand__tagline { font-size: 10px; font-weight: 600; margin-top: 4px; padding-left: 100px; }
  .services { font-size: 16.5px; line-height: 22px; margin-top: 18px; }
  .products {
    display: flex; justify-content: space-between;
    margin: 25px 63px 0 66px;
  }
  .product {
    width: 120px; height: 96px; border-radius: 5px; background: var(--paper); padding: 8px;
  }
  .product__fill { width: 100%; height: 100%; border-radius: 3px; }
  .product__fill--copier { background: var(--thumb-copier); }
  .product__fill--paper { background: var(--thumb-paper); }
  .product__fill--ink { background: var(--thumb-ink); opacity: .8; }
</style>
</head>
<body>
<main class="canvas">

  <section class="card card--front">
    <div class="holder">
      <p class="holder__name">Maren Tolley</p>
      <p class="holder__role">Sales Executive</p>
      <p class="holder__address">14A Larkfield Avenue<br>#05-112<br>Singapore 530418</p>
      <ul class="contact">
        <li><svg viewBox="0 0 10 10"><path d="M3 0h4a1 1 0 0 1 1 1v8a1 1 0 0 1-1 1H3a1 1 0 0 1-1-1V1a1 1 0 0 1 1-1zm0 1.5v6h4v-6z"/></svg>9000 4716</li>
        <li><svg viewBox="0 0 10 10"><path d="M0 2h10v6H0zM.6 2.4 5 5.6l4.4-3.2"/></svg>maren@tonerbay.sg</li>
        <li><svg viewBox="0 0 10 10"><circle cx="5" cy="5" r="5"/></svg>www.tonerbay.sg</li>
      </ul>
    </div>
    <div class="divider"></div>
    <div class="front-brand">
      <div class="front-brand__mark"></div>
      <p class="front-brand__name">tonerbay.sg</p>
    </div>
  </section>

  <section class="card card--back">
    <div class="brand">
      <span class="brand__square"></span>
      <span class="brand__name">tonerbay.sg</span>
    </div>
    <p class="brand__tagline">Compatible printer ink and toner solutions</p>
    <p class="services">Printer Ink &amp; Toner Catridge | Orginal Printer Catridge<br>Paper Product | Printer Maintance &amp; Repair</p>
    <div class="products">
      <div class="product"><div class="product__fill product__fill--copier" role="img" aria-label="Office laser printer and copier"></div></div>
      <div class="product"><div class="product__fill product__fill--paper" role="img" aria-label="Stacked reams of A4 paper"></div></div>
      <div class="product"><div class="product__fill product__fill--ink" role="img" aria-label="Cyan, magenta, yellow and black ink cartridges"></div></div>
    </div>
  </section>

</main>
</body>
</html>
```